Clear Plastic Card Design

I am looking to have a business card designed from my logo icon. I am looking to match the style of a different business card I have attached in the files.
Looking for a card that is plastic, with layers of transparency in the shape of my logo icon (also attached in the files) - not a circle like the other card. The winning design will incorporate the red icon logo on the front and back and include the charity's name, "Light for the Weary Souls" in the same or similar font, as well as an email and phone number. For now, use the email: email@lightfortheweary-mail.org and the phone number 555-382-7194.
We like how the sample business card has transparency, partial and full opacity layers and a matching color scheme. Files will need to be in vector so that our business card printing company can work with it.
UPDATE:
We've some excellent designs in, thank you everyone! I got an early review from the owner, and he requested a minor redirect to find his perfect design. He wants the design to stand out by NOT being a rectangle. Try instead a circle, square, or best yet - something that falls in the outline of the logo icon, either fully or partially. Thank you, everyone!
Light for the Weary Souls text should be incorporated as well as a phone and email.

```html
<!DOCTYPE html>
<html lang="en">
<head>
<meta charset="utf-8">
<title>Light for the Weary Souls – Business Card</title>
<link rel="stylesheet" href="https://fonts.googleapis.com/css2?family=Roboto+Condensed:wght@700&display=swap">
<style>
  :root {
    --page-bg: #ecebea;
    --card-red-deep: #c8101e;
    --card-red: #d8222a;
    --card-red-warm: #e64a2c;
    --card-orange: #ec5a24;
    --text-white: #ffffff;
    --foil-silver: #ece8e8;
  }
  * { margin: 0; padding: 0; box-sizing: border-box; }
  html, body {
    width: 1200px;
    height: 900px;
    overflow: hidden;
    background: var(--page-bg);
  }
  .canvas {
    position: relative;
    width: 1200px;
    height: 900px;
    display: flex;
    align-items: center;
    justify-content: center;
  }
  .business-card {
    position: relative;
    width: 1000px;
    height: 620px;
    overflow: hidden;
    font-family: "Roboto Condensed", "Arial Narrow", sans-serif;
    font-weight: 700;
    color: var(--text-white);
    box-shadow: 0 18px 40px rgba(0,0,0,0.18);
  }
  .card-texture {
    position: absolute;
    inset: 0;
    background:
      radial-gradient(ellipse at 30% 80%, var(--card-red-deep) 0%, transparent 60%),
      linear-gradient(120deg, var(--card-red) 0%, var(--card-red-deep) 40%, var(--card-red-warm) 80%, var(--card-orange) 100%);
  }
  .charity-name {
    position: absolute;
    left: 44px;
    top: 62px;
    font-size: 68px;
    line-height: 76px;
    text-transform: uppercase;
    letter-spacing: -0.5px;
  }
  .contact {
    position: absolute;
    left: 54px;
    top: 450px;
  }
  .contact-phone {
    display: flex;
    align-items: center;
    gap: 10px;
    font-size: 50px;
    line-height: 56px;
    letter-spacing: 0.5px;
  }
  .phone-icon { width: 54px; height: 54px; flex: none; }
  .contact-email {
    margin-top: 8px;
    font-size: 34px;
    line-height: 40px;
    letter-spacing: -0.3px;
  }
  .logo-mark {
    position: absolute;
    left: 400px;
    top: 110px;
    width: 570px;
    height: 340px;
    display: flex;
    align-items: center;
    justify-content: center;
    text-align: center;
    font-size: 74px;
    line-height: 80px;
    text-transform: uppercase;
    color: var(--foil-silver);
    opacity: 0.88;
  }
</style>
</head>
<body>
<main class="canvas">
  <article class="business-card">
    <div class="card-texture" role="img" aria-label="Red faceted low-poly background texture shading to orange on the right"></div>

    <h1 class="charity-name">Light for<br>the Weary<br>Souls</h1>

    <div class="logo-mark">Light for the Weary Souls</div>

    <div class="contact">
      <p class="contact-phone">
        <svg class="phone-icon" viewBox="0 0 54 54" aria-hidden="true">
          <circle cx="27" cy="27" r="27" fill="#ffffff"/>
          <path d="M19 15c1.5-1 3-.5 3.8.8l2.4 4c.7 1.2.4 2.6-.6 3.4l-1.6 1.2c1.2 2.8 3.4 5 6.2 6.3l1.2-1.6c.8-1 2.3-1.3 3.4-.6l4 2.4c1.3.8 1.7 2.4.8 3.8l-1.3 2c-1 1.5-2.9 2.2-4.6 1.7C24.5 36.5 17.5 29.5 15.6 21.3c-.4-1.7.2-3.5 1.7-4.5z" fill="var(--card-red)"/>
          <path d="M30 14a10 10 0 0 1 10 10M30 19a5 5 0 0 1 5 5" stroke="var(--card-red)" stroke-width="2.4" fill="none" stroke-linecap="round"/>
        </svg>
        <span>555-382-7194</span>
      </p>
      <p class="contact-email">email@lightfortheweary-mail.org</p>
    </div>
  </article>
</main>
</body>
</html>
```